Simple and Clean business card design

We would like the design to be simple clean and to incorporate our colors.

We are open to your design and talent, we have the dots in our logo as we think of it as data points and we connect data points for people.

We are open to see the great creative and clean design you bring to the table

Contact Information for Business Card

please include: name, position, email, phone and website

Font styles to use
Sans Serif

Requirements
Must have
• my colors incorporated, simplicity
Nice to have
• lots of white space, simplicity
Should not have
• complexicity/ complex art

```html
<!DOCTYPE html>
<html lang="en">
<head>
<meta charset="utf-8">
<title>Nodera — Business Card</title>
<link rel="stylesheet" href="https://fonts.googleapis.com/css2?family=Montserrat:wght@400;500;600;700&display=swap">
<style>
  :root {
    --backdrop: #2b2b2e;
    --card: #1c1d1f;
    --white: #ffffff;
    --muted: #9a9b9e;
    --yellow: #f6c21c;
    --green: #34a853;
    --blue: #5b80c6;
    --red: #e94235;
  }
  * { margin: 0; padding: 0; box-sizing: border-box; }
  html, body {
    width: 1200px; height: 909px; overflow: hidden;
    background: var(--backdrop);
    font-family: "Montserrat", sans-serif;
    color: var(--white);
  }
  .card {
    position: absolute;
    left: 290px;
    width: 620px; height: 354px;
    background: var(--card);
    box-shadow: 0 10px 30px rgba(0,0,0,.45);
  }
  .card--front { top: 80px; }
  .card--back { top: 474px; }

  /* front */
  .brand {
    position: absolute; left: 48px; top: 40px;
    display: flex; align-items: center; gap: 12px;
  }
  .brand__name {
    font-size: 56px; font-weight: 700; letter-spacing: -1px;
    color: var(--white); line-height: 1;
  }
  .brand__dot {
    width: 22px; height: 22px; border-radius: 50%;
    background: var(--blue);
  }
  .person { position: absolute; left: 48px; top: 132px; }
  .person__name {
    font-size: 24px; font-weight: 600; text-transform: uppercase; letter-spacing: .5px;
  }
  .person__first { color: var(--yellow); }
  .person__title { font-size: 19px; font-weight: 400; margin-top: 2px; }
  .contacts {
    position: absolute; left: 48px; top: 222px;
    list-style: none; font-size: 15px; font-weight: 500;
  }
  .contacts li { display: flex; align-items: center; gap: 10px; height: 28px; }
  .contacts svg { width: 14px; height: 14px; flex: none; }
  .divider {
    position: absolute; left: 322px; top: 248px;
    width: 2px; height: 46px; background: var(--white);
    transform: rotate(18deg);
  }
  .address {
    position: absolute; left: 346px; top: 248px;
    font-size: 15px; font-weight: 500; line-height: 23px; font-style: normal;
  }

  /* back */
  .back-brand {
    position: absolute; left: 0; right: 0; top: 120px;
    display: flex; justify-content: center; align-items: center; gap: 14px;
  }
  .back-brand .brand__name { font-size: 60px; }
  .back-brand .brand__dot { width: 24px; height: 24px; }
  .back-url {
    position: absolute; left: 0; right: 0; top: 262px;
    text-align: center; font-size: 16px; letter-spacing: 4px;
    color: var(--muted);
  }
</style>
</head>
<body>
  <section class="card card--front" aria-label="Business card front">
    <div class="brand">
      <span class="brand__name">Nodera</span>
      <span class="brand__dot"></span>
    </div>

    <div class="person">
      <h1 class="person__name"><span class="person__first">Marcus</span> Ellery</h1>
      <p class="person__title">Founder/ CEO</p>
    </div>

    <ul class="contacts">
      <li>
        <svg viewBox="0 0 24 24" aria-hidden="true"><path fill="var(--yellow)" d="M6.6 10.8a15 15 0 0 0 6.6 6.6l2.2-2.2a1 1 0 0 1 1-.25 11.4 11.4 0 0 0 3.6.57 1 1 0 0 1 1 1V20a1 1 0 0 1-1 1A17 17 0 0 1 3 4a1 1 0 0 1 1-1h3.5a1 1 0 0 1 1 1c0 1.25.2 2.45.57 3.6a1 1 0 0 1-.25 1z"/></svg>
        <span>555-014-2736</span>
      </li>
      <li>
        <svg viewBox="0 0 24 24" aria-hidden="true"><path fill="var(--yellow)" d="M2 5h20v14H2z"/><path fill="none" stroke="var(--card)" stroke-width="2" d="M2 5l10 8 10-8"/></svg>
        <span>marcus.ellery@nodera.one</span>
      </li>
      <li>
        <svg viewBox="0 0 24 24" aria-hidden="true"><circle cx="12" cy="12" r="10" fill="var(--yellow)"/><path fill="none" stroke="var(--card)" stroke-width="1.6" d="M2 12h20M12 2c3 3 3 17 0 20M12 2c-3 3-3 17 0 20"/></svg>
        <span>www.nodera.one</span>
      </li>
    </ul>

    <span class="divider" aria-hidden="true"></span>
    <address class="address">18 W. Elm Avenue<br>Brookfield, IL 60513</address>
  </section>

  <section class="card card--back" aria-label="Business card back">
    <div class="back-brand">
      <span class="brand__name">Nodera</span>
      <span class="brand__dot"></span>
    </div>
    <p class="back-url">www.nodera.one</p>
  </section>
</body>
</html>
```